NZ First of it's kind solutions directory and marketplace for busy Mums needs a business card design

We need a business card design for our new nationwide business in NZ (long term plans to go global). We provide solutions to the everyday challenges that busy Mums face by connecting them with quality communities and suppliers of carefully selected, relevant products and services. We sell direct via our online marketplace. The final design should communicate our values of inclusivity, quality and smart solutions. Colours should incorporate our logo colour palette of #477077 and #6ba8b2. Our website is at https://www.brightnestmums.example

Target Market(s)

busy Mums, Age 28 – 50, female, income over $100K, location main centres NZ primarily but NZ wide. Is likely juggling work or career with a young family. Probably had hobbies which have fallen by the wayside.
-Wants to succeed in her chosen career without compromising on family life
-to successfully juggle her career without feeling like she is compromising her children
- Is time poor, something always has to give and it’s generally her health (she’ll stay up late, get stressed)
- probably ex corporate or professional career. Has discretional income

Industry/Entity Type

Business

Contact Information for Business Card

Lena Forbisher, Founder, BrightNestMums.example (Strapline Tap; Gather; Sorted), 47 Kowhai Terrace, Ellerslie, Auckland 1051, New Zealand. Mob: 021 483 517 Ph: +64 (0)9 571 4860

Font styles to use
Other font styles liked:
• Raleway, and/or Architects Daughter

Colors
00a990
33b8a4
86cfc6
cfeae6

Requirements
Must have
• the above details, streamline. the logo and colours associated with those logos
Should not have
• foil or metallic colours

```html
<!DOCTYPE html>
<html lang="en">
<head>
<meta charset="utf-8">
<title>BrightNestMums Business Card</title>
<link rel="stylesheet" href="https://fonts.googleapis.com/css2?family=Roboto:wght@400;500;700&family=Roboto+Condensed:wght@700&display=swap">
<style>
  :root {
    --backdrop: #2b2b2b;
    --teal-dark: #477077;
    --teal-light: #6ba8b2;
    --card-white: #f2f2f2;
    --ink: #4a4a4a;
    --white: #ffffff;
  }
  * { margin: 0; padding: 0; box-sizing: border-box; }
  html, body {
    width: 1200px;
    height: 960px;
    overflow: hidden;
    background: var(--backdrop);
    font-family: "Roboto", Arial, sans-serif;
  }
  .canvas {
    position: relative;
    width: 1200px;
    height: 960px;
  }
  .card {
    position: absolute;
    width: 600px;
    height: 343px;
    box-shadow: 0 3px 8px rgba(0,0,0,0.5);
  }
  .card-front {
    left: 314px;
    top: 113px;
    background: var(--card-white);
  }
  .side-band {
    position: absolute;
    left: 0;
    top: 0;
    width: 48px;
    height: 100%;
    background: var(--teal-dark);
  }
  .brand {
    position: absolute;
    left: 28px;
    top: 40px;
    display: flex;
    align-items: center;
    gap: 10px;
  }
  .brand-dot {
    width: 30px;
    height: 30px;
    border-radius: 50%;
    background: var(--teal-dark);
    border: 3px solid var(--white);
  }
  .brand-name {
    font-family: "Roboto", Arial, sans-serif;
    font-weight: 700;
    font-size: 28px;
    color: var(--teal-dark);
    letter-spacing: -0.3px;
  }
  .details {
    position: absolute;
    right: 28px;
    top: 155px;
    text-align: right;
  }
  .person-name {
    font-family: "Roboto Condensed", "Arial Narrow", sans-serif;
    font-weight: 700;
    font-size: 22px;
    color: var(--teal-dark);
    line-height: 26px;
  }
  .person-role {
    font-weight: 500;
    font-size: 15px;
    color: var(--teal-light);
    line-height: 20px;
    letter-spacing: 0.3px;
    margin-bottom: 14px;
  }
  .contact-list {
    list-style: none;
    font-size: 14.5px;
    color: var(--ink);
    line-height: 19px;
  }
  .contact-list li {
    display: flex;
    justify-content: flex-end;
    align-items: center;
    gap: 7px;
  }
  .contact-icon {
    width: 13px;
    height: 13px;
    flex: none;
  }
  .address {
    margin-top: 7px;
    font-size: 14.5px;
    color: var(--ink);
    line-height: 18px;
    font-style: normal;
  }
  .card-back {
    left: 311px;
    top: 472px;
    background: var(--teal-light);
  }
  .back-mark {
    position: absolute;
    left: 50%;
    top: 75px;
    transform: translateX(-50%);
    display: flex;
    flex-direction: column;
    align-items: center;
    gap: 18px;
  }
  .back-dot {
    width: 110px;
    height: 110px;
    border-radius: 50%;
    background: var(--white);
  }
  .back-name {
    font-weight: 700;
    font-size: 30px;
    color: var(--white);
  }
  .strapline {
    position: absolute;
    left: 0;
    right: 0;
    top: 305px;
    text-align: center;
    font-size: 14.5px;
    color: var(--white);
  }
</style>
</head>
<body>
<main class="canvas">
  <section class="card card-front">
    <div class="side-band"></div>
    <div class="brand">
      <span class="brand-dot"></span>
      <span class="brand-name">BrightNestMums</span>
    </div>
    <div class="details">
      <h1 class="person-name">LENA FORBISHER</h1>
      <p class="person-role">FOUNDER</p>
      <ul class="contact-list">
        <li>+64 (0)9 571 4860
          <svg class="contact-icon" viewBox="0 0 16 16"><path fill="#477077" d="M3.6 1.2l2.3 2.6c.4.4.3 1-.1 1.4L4.7 6.3c.9 2 2.6 3.8 4.8 4.9l1.2-1.1c.4-.4 1-.4 1.4 0l2.5 2.3c.4.4.4 1 0 1.4l-1.3 1.3C11 16.5 6.6 14 3.8 11 1 8 -.5 4 1 2.2L2.2 1.1c.4-.3 1-.3 1.4.1z"/></svg>
        </li>
        <li>021 483 517
          <svg class="contact-icon" viewBox="0 0 16 16"><rect x="3.5" y="0.8" width="9" height="14.4" rx="1.5" fill="none" stroke="#477077" stroke-width="1.6"/><rect x="7" y="12.2" width="2" height="1.2" fill="#477077"/></svg>
        </li>
        <li>BrightNestMums.example
          <svg class="contact-icon" viewBox="0 0 16 16"><circle cx="8" cy="8" r="7" fill="#477077"/><path d="M5 4c1.5 1 1 2.5 2.5 3S8 9.5 6.5 11M10 3c0 1.5 1.5 2 2.5 2.5M10.5 9.5c1 .5 1.5 1.5 1.5 3" stroke="#f2f2f2" stroke-width="1.3" fill="none"/></svg>
        </li>
      </ul>
      <address class="address">47 Kowhai Terrace, Ellerslie<br>Auckland 1051, New Zealand</address>
    </div>
  </section>

  <section class="card card-back">
    <div class="back-mark">
      <span class="back-dot"></span>
      <span class="back-name">BrightNestMums</span>
    </div>
    <p class="strapline">Tap; Gather; Sorted</p>
  </section>
</main>
</body>
</html>
```